Sell the dream! Property investment proposal document

We are looking for a proposal document which outlines our vision for property development. The purpose of the document is to raise investment from investors - sell the dream!
Brief summary:
Kestrel Dwellings Developments, is an emerging New Zealand property investment company with a focus on providing unique property investment opportunities.
Our expertise and capabilities in architectural modular homes provide us with a remarkable advantage in tackling the development of properties that are typically considered challenging, remote, or uniquely positioned.
Our specialization in this niche sector of property development not only sets us apart from competitors, but also paves the way for lucrative investment opportunities in the New Zealand property market.
Feel free to use any images from www.kestreldwellings.co.nz
Target Market(s)
investors for a unique property development opportunity
Industry/Entity Type
luxury property development in unique locations throughout New Zealand
Colors
Designer to choose only greyscale colors for use in the design.
Look and feel

```html
<!DOCTYPE html>
<html lang="en">
<head>
<meta charset="utf-8">
<title>Kestrel Dwellings Developments – Proposal Spreads</title>
<link href="https://fonts.googleapis.com/css2?family=Archivo:wght@300;400;500;600;700&display=swap" rel="stylesheet">
<style>
  :root {
    --backdrop: #ececec;
    --ink-dark: #161616;
    --ink-darker: #121212;
    --paper-white: #f4f4f4;
    --text-light: #e6e6e6;
    --text-dark: #2a2a2a;
    --dot-on: #cfcfcf;
    --dot-mid: #9a9a9a;
    --dot-off: #4a4a4a;
  }
  * { margin: 0; padding: 0; box-sizing: border-box; }
  html, body { width: 896px; height: 1200px; overflow: hidden; }
  body {
    background: var(--backdrop);
    font-family: "Archivo", Arial, sans-serif;
    position: relative;
  }
  .spread {
    position: absolute;
    left: 68px;
    width: 760px;
    height: 298px;
    overflow: hidden;
    box-shadow: 0 2px 6px rgba(0,0,0,0.12);
  }
  .spread--overview { top: 150px; }
  .spread--origins { top: 752px; }

  .gutter {
    position: absolute;
    top: 0; bottom: 0;
    left: 370px;
    width: 20px;
    background: linear-gradient(90deg, rgba(0,0,0,0) 0%, rgba(0,0,0,0.18) 50%, rgba(255,255,255,0.08) 55%, rgba(0,0,0,0) 100%);
    pointer-events: none;
  }

  .photo { position: absolute; }
  .photo--cabin-deck {
    left: 0; top: 0; width: 471px; height: 298px;
    background:
      linear-gradient(180deg, #b9c7da 0%, #cfd7e0 30%, rgba(0,0,0,0) 42%),
      linear-gradient(180deg, rgba(0,0,0,0) 40%, #2a2a2a 45%, #1d1d1d 70%, #5a5048 80%, #4a4a3c 100%);
  }
  .photo--glass-pavilion {
    left: 0; top: 0; width: 142px; height: 298px;
    background: linear-gradient(180deg, #a9b3c1 0%, #c9c8c4 45%, #d8c7a4 58%, #6f7275 66%, #4b4a47 80%, #5b5650 100%);
  }
  .photo--coastal-cabin {
    left: 555px; top: 0; width: 205px; height: 144px;
    background: linear-gradient(180deg, #b8c8d8 0%, #9fb1c0 20%, #5f6b60 40%, #4a5244 70%, #6a6a5a 100%);
  }
  .photo--bedroom {
    left: 555px; top: 151px; width: 205px; height: 147px;
    background: linear-gradient(90deg, #3a3632 0%, #8a8478 30%, #b9b5a8 55%, #5c5650 80%, #2e2c2a 100%);
  }
  .photo-gap {
    position: absolute; left: 555px; top: 144px; width: 205px; height: 7px;
    background: var(--paper-white);
  }

  .panel { position: absolute; top: 0; height: 298px; }
  .panel--dark { background: var(--ink-dark); color: var(--text-light); }
  .panel--overview { left: 471px; width: 289px; padding: 50px 24px 0 39px; }
  .panel--origins {
    left: 142px; width: 238px; padding: 52px 20px 0 31px;
    background: linear-gradient(160deg, #242424 0%, var(--ink-darker) 45%, #1a1a1a 100%);
  }
  .panel--light {
    left: 380px; width: 175px; padding: 50px 20px 0 35px;
    background: linear-gradient(90deg, #e2e2e2 0%, var(--paper-white) 12%, #fafafa 100%);
    color: var(--text-dark);
  }

  .section-title {
    font-size: 13px;
    line-height: 16px;
    letter-spacing: 2.6px;
    text-transform: uppercase;
  }
  .section-title .light { font-weight: 300; }
  .section-title .bold { font-weight: 700; }
  .section-title--stacked .bold,
  .section-title--stacked .light { display: block; }
  .panel--light .section-title { letter-spacing: 0.3px; font-size: 13px; color: #333; }
  .panel--light .section-title .bold { color: #222; }

  .dots { display: flex; gap: 6px; margin: 12px 0 0; }
  .dots span { width: 4px; height: 4px; border-radius: 50%; background: var(--dot-on); }
  .dots span:nth-child(2) { background: #bdbdbd; }
  .dots span:nth-child(3) { background: var(--dot-mid); }
  .dots span:nth-child(4) { background: var(--dot-off); }
  .panel--light .dots span { background: #777; }
  .panel--light .dots span:nth-child(3) { background: #aaa; }
  .panel--light .dots span:nth-child(4) { background: #ddd; }

  .body-copy { font-size: 5.3px; line-height: 7.8px; font-weight: 400; }
  .body-copy p { margin-bottom: 7.6px; }
  .body-copy strong { font-weight: 700; }
  .panel--overview .body-copy { margin-top: 32px; width: 226px; }
  .panel--origins .body-copy { margin-top: 28px; width: 184px; }
  .panel--origins .body-copy p.tight { margin-bottom: 0; }
  .panel--light .body-copy { margin-top: 28px; width: 100px; }
</style>
</head>
<body>

<section class="spread spread--overview">
  <div class="photo photo--cabin-deck" role="img" aria-label="Black timber modular cabin with a wide wooden deck among coastal shrubs at dusk"></div>
  <div class="panel panel--dark panel--overview">
    <h2 class="section-title"><span class="light">Business</span> <span class="bold">Overview</span></h2>
    <div class="dots"><span></span><span></span><span></span><span></span></div>
    <div class="body-copy">
      <p><strong>Kestrel Dwellings Developments,</strong> is an emerging New Zealand property investment company with a focus on providing unique property investment opportunities.</p>
      <p>Our expertise and capabilities in architectural modular homes provide us with a remarkable advantage in tackling the development of properties that are typically considered challenging, remote, or uniquely positioned.</p>
      <p>As a company, with 48 employees boasting a wealth of experience in handling complex architectural projects, making us well-equipped to navigate the intricacies and demands of such ventures.</p>
      <p>This advantage allows us to not only execute projects efficiently but also to deliver exceptional results within condensed time frames.</p>
      <p>By capitalizing on our ability to develop difficult, remote, or one-of-a-kind properties swiftly and effectively, Kestrel Dwellings Developments offers investors a rare chance to engage in projects that promise exceptional profitability in the New Zealand property market.</p>
      <p>Our specialization in this niche sector of property development not only sets us apart from competitors, but also paves the way for lucrative investment opportunities in the New Zealand property market.</p>
    </div>
  </div>
  <div class="gutter"></div>
</section>

<section class="spread spread--origins">
  <div class="photo photo--glass-pavilion" role="img" aria-label="Glass pavilion home on a pebble shore at sunset"></div>
  <div class="panel panel--origins" style="color: var(--text-light);">
    <h2 class="section-title section-title--stacked"><span class="light">Business</span><span class="bold">Origins</span></h2>
    <div class="dots"><span></span><span></span><span></span><span></span></div>
    <div class="body-copy">
      <p><strong>Kestrel Dwellings Developments</strong> was established with the goal of transforming the property investment market in New Zealand by introducing an innovative approach that centers on architectural modular designs and streamlined project timelines.</p>
      <p>Driven by our enthusiasm for architecture and real estate, we have expanded our successful business model to not only offer financial opportunities for investors but also to expand on our passion for high-end architectural design. With a wealth of experience accumulated over the past six years in the construction and the property market, we are pivoting to focus solely on our property development initiatives, presenting completed Kestrel projects to the market, in exclusive locations.</p>
      <p class="tight">These projects will boast high-quality standards, meticulous attention to detail and landscaping, and creative design elements.</p>
      <p>By introducing completed Kestrel properties into the market, we aim to reach a wider audience, catering to individuals who prefer ready-to-occupy homes, over engaging in the design and construction process. This approach also simplifies the financing process for prospective buyers, as established properties are often preferred by financial lenders.</p>
    </div>
  </div>
  <div class="panel panel--light">
    <h2 class="section-title section-title--stacked"><span class="light">Competitive</span><span class="bold">Advantage</span></h2>
    <div class="dots"><span></span><span></span><span></span><span></span></div>
    <div class="body-copy">
      <p>Our competitive advantage lies in the uniqueness of our property investment opportunities. Unlike traditional real estate companies, we focus on offering properties that are not only profitable but also aesthetically pleasing and unique.</p>
      <p>By catering to the tastes of architecture lovers, we set ourselves apart from the competition and attract a niche market of customers who appreciate the artistry and design of our projects.</p>
      <p>Additionally, the streamlined and condensed timelines facilitated by our modular approach provide quicker returns on investment.</p>
    </div>
  </div>
  <div class="photo photo--coastal-cabin" role="img" aria-label="Timber cabin on a clifftop above the ocean"></div>
  <div class="photo-gap"></div>
  <div class="photo photo--bedroom" role="img" aria-label="Bedroom with floor-to-ceiling windows and sheer curtains opening to a garden"></div>
  <div class="gutter"></div>
</section>

</body>
</html>
```